SnackOrbit!!! A Vending Machine Business Looking for an attractive website.

We are a vending machine business in Northern Michigan. We have changed our name and have rebranded our company. We would like an attractive website that shares who we are, what services we provide, the products we offer in our machines, along with a form businesses can fill out to see if they are a good fit for our company. I would like to have a Home Page, About SnackOrbit, Why Choose SnackOrbit?, Products & Services, Contact Us (With a Login Option), and a page with a questionnaire for thos interested in getting a FREE Vending Machine.

Target Market(s)

Businesses, Campgrounds, Schools, and many more in Northern Michigan

Industry/Entity Type

Vending Machines

Coding

Coded - Design and coding required

Number of Pages Required

5+ page

Requirements
Must have
• An inviting and enticing Home Page. I want to get my potential clients engaged in our website.
Nice to have
• Possibly background photos from Northern Michigan
Should not have
• A corporate feel. I do not want a boring website.

```html
<!DOCTYPE html>
<html lang="en">
<head>
<meta charset="utf-8">
<title>SnackOrbit – Elevate Your Snack Game</title>
<link href="https://fonts.googleapis.com/css2?family=Bebas+Neue&family=Poppins:wght@400;500;600&display=swap" rel="stylesheet">
<style>
:root{
  --navy:#1b1d5a;
  --navy-deep:#14164a;
  --green:#2c5a2a;
  --green-deep:#1f4420;
  --orange:#f47b16;
  --grey:#eeeeee;
  --ink:#2a2a2a;
  --white:#ffffff;
  --line:#cfcfcf;
}
*{box-sizing:border-box;margin:0;padding:0}
html,body{width:1200px;height:3962px;overflow:hidden}
body{position:relative;font-family:"Poppins",sans-serif;color:var(--ink);background:var(--white)}
.abs{position:absolute}
.display{font-family:"Bebas Neue",sans-serif;font-weight:400;letter-spacing:.5px}
.btn{position:absolute;display:flex;align-items:center;justify-content:center;font-family:"Bebas Neue",sans-serif;font-size:22px;letter-spacing:.5px;color:var(--white);text-decoration:none}
.btn--green{background:var(--green);border-radius:30px}
.btn--orange{background:var(--orange)}
.photo{position:absolute}

/* hero */
.hero{position:absolute;left:0;top:0;width:1200px;height:646px;background:linear-gradient(180deg,#3a4a63 0%,#7a6a58 35%,#c98a4a 55%,#3b3530 80%,#1e1d22 100%)}
.hero__shade{position:absolute;inset:0;background:rgba(10,12,25,.35)}
.brand{position:absolute;font-family:"Bebas Neue",sans-serif;color:var(--white);display:flex;align-items:center;gap:10px}
.brand__dot{width:22px;height:22px;border-radius:50%;background:var(--white)}
.nav{position:absolute;left:411px;top:42px;display:flex;gap:26px;font-family:"Bebas Neue",sans-serif;font-size:17px;color:var(--white);letter-spacing:.4px}
.login{position:absolute;left:1051px;top:32px;width:76px;height:38px;background:var(--orange);border-radius:3px;display:flex;align-items:center;justify-content:center;gap:6px;font-family:"Bebas Neue",sans-serif;font-size:17px;color:var(--white)}
.hero__title{position:absolute;left:0;width:1200px;top:218px;text-align:center;font-size:124px;line-height:1;color:var(--white)}
.hero__tag{position:absolute;left:0;width:1200px;top:344px;text-align:center;font-size:31px;font-weight:500;color:var(--white)}
.hero__cta{left:452px;top:408px;width:296px;height:46px;background:var(--green);border:2px solid var(--white);border-radius:30px;font-size:21px}

/* machines */
.machine{position:absolute;border-radius:8px;background:linear-gradient(160deg,#2b2b35 0%,#4a4a56 25%,#9a9aa0 70%,#7a7a80 100%)}

/* about */
.about__title{left:524px;top:712px;font-size:44px;color:var(--navy)}
.about__text{left:524px;top:773px;width:600px;font-size:13px;line-height:25px;color:var(--ink)}

/* products */
.products{position:absolute;left:0;top:1100px;width:1200px;height:550px;background:var(--grey)}
.section-title{position:absolute;left:0;width:1200px;text-align:center;font-size:44px;color:var(--navy)}
.products__lead{position:absolute;left:180px;width:840px;top:1220px;text-align:center;font-size:13px;line-height:25px}
.arch{position:absolute;top:1300px;width:329px;height:350px;background:var(--green);border-radius:165px 165px 0 0}
.arch__label{position:absolute;top:1342px;width:329px;text-align:center;font-family:"Bebas Neue",sans-serif;font-size:32px;line-height:32px;color:var(--white)}

/* services */
.card{position:absolute;width:512px;height:243px;border-radius:8px;background:linear-gradient(135deg,var(--green) 0%,#213c38 45%,var(--navy) 100%);color:var(--white)}
.card__icon{position:absolute;left:20px;top:24px;width:64px;height:64px;border-radius:50%;background:var(--white);display:flex;align-items:center;justify-content:center}
.card__title{position:absolute;left:104px;font-family:"Bebas Neue",sans-serif;font-size:32px;line-height:30px}
.card__text{position:absolute;left:20px;right:30px;font-size:12.5px;line-height:23px}

/* cta band */
.band{position:absolute;left:0;width:1200px}
.band__title{position:absolute;left:0;width:1200px;text-align:center;font-size:44px;line-height:46px;color:var(--white)}
.band__text{position:absolute;left:300px;width:600px;text-align:center;font-size:13px;line-height:25px;color:var(--white)}

/* contact */
.contact__title{left:74px;top:2918px;font-size:44px;color:var(--navy)}
.field{position:absolute;height:46px;border:1px solid var(--line);border-radius:24px;padding-left:22px;display:flex;align-items:center;font-size:13px;color:#555}
.field--area{height:112px;border-radius:14px;align-items:flex-start;padding-top:16px}

/* footer */
.foot-head{position:absolute;top:3700px;font-family:"Bebas Neue",sans-serif;font-size:24px;color:var(--navy)}
.foot-link{position:absolute;left:363px;font-size:13px;color:#333}
.foot-row{position:absolute;left:615px;display:flex;gap:14px;font-size:13px;line-height:22px;color:#333}
.foot-row svg{flex:none;margin-top:4px}
.social{position:absolute;top:3745px;left:884px;display:flex;gap:18px}
.social span{width:22px;height:22px;border-radius:50%;background:var(--green)}
</style>
</head>
<body>

<!-- hero -->
<section class="hero">
  <div class="photo" style="inset:0;background:linear-gradient(180deg,#34445c 0%,#5d5b66 30%,#b07a48 50%,#4a3b30 75%,#1c1b20 100%)" role="img" aria-label="City skyline at dusk with lit streets"></div>
  <div class="hero__shade"></div>
  <div class="brand" style="left:76px;top:28px;font-size:44px"><span class="brand__dot"></span>SnackOrbit</div>
  <nav class="nav"><span>Home</span><span>About SnackOrbit</span><span>Why Choose SnackOrbit?</span><span>Products &amp; Services</span><span>Contact Us</span></nav>
  <div class="login"><svg width="12" height="13" viewBox="0 0 12 13"><rect x="1" y="5.5" width="10" height="7" rx="1" fill="#fff"/><path d="M3.5 5.5V4a2.5 2.5 0 0 1 5 0v1.5" stroke="#fff" stroke-width="1.6" fill="none"/></svg>Login</div>
  <h1 class="hero__title display">SnackOrbit</h1>
  <p class="hero__tag">Elevate Your Snack Game!</p>
  <a class="btn hero__cta">Get a Free Vending Machine</a>
</section>

<!-- about -->
<svg class="abs" style="left:0;top:546px" width="490" height="520" viewBox="0 0 490 520" aria-hidden="true">
  <path d="M0 110 C90 20 250 -10 360 40 C470 95 500 250 420 340 C380 385 330 400 270 420 L0 515 Z" fill="#1b1d5a"/>
</svg>
<div class="machine" style="left:108px;top:585px;width:266px;height:449px" role="img" aria-label="Snack vending machine stocked with chips and candy"></div>
<h2 class="abs display about__title">Who We Are</h2>
<p class="abs about__text">Welcome to SnackOrbit, where snacking meets delight! We’re not just about vending machines; we’re your culinary companions, your flavor curators, and your secret stash of happiness. Marcus and Elena, the dynamic duo behind SnackOrbit, have a passion for all things tasty. With backgrounds in sales and a penchant for personal connections, they’ve transformed the vending experience into an art form.</p>
<a class="btn btn--green" style="left:524px;top:927px;width:180px;height:47px">Read More</a>

<!-- products -->
<section class="products"></section>
<h2 class="section-title display" style="top:1152px">Products We Offer</h2>
<p class="products__lead">At SnackOrbit, we don’t just vend snacks—we curate cravings. Our customized vending solutions bring flavor, convenience, and community to Northern Michigan.</p>

<div class="arch" style="left:74px"></div>
<div class="arch__label" style="left:74px">Mid-Morning<br>Snack</div>
<div class="machine" style="left:142px;top:1425px;width:192px;height:328px" role="img" aria-label="Snack vending machine"></div>

<div class="arch" style="left:434px"></div>
<div class="arch__label" style="left:434px">Refreshing<br>Beverage</div>
<div class="machine" style="left:502px;top:1425px;width:192px;height:328px;background:linear-gradient(160deg,#2b2b35 0%,#5a4a5a 25%,#a58a9e 70%,#7e6a7a 100%)" role="img" aria-label="Beverage vending machine"></div>

<div class="arch" style="left:797px"></div>
<div class="arch__label" style="left:797px">Satisfying<br>Breakfast Burrito</div>
<div class="machine" style="left:865px;top:1425px;width:192px;height:328px;background:linear-gradient(160deg,#2b2b35 0%,#4a5266 25%,#8a9ab8 70%,#6a7690 100%)" role="img" aria-label="Fresh food vending machine"></div>

<!-- services -->
<h2 class="section-title display" style="top:1812px">Services We Provide</h2>

<article class="card" style="left:74px;top:1909px">
  <div class="card__icon"><svg width="30" height="30" viewBox="0 0 30 30"><path d="M15 3a8 8 0 0 0-8 8c0 6 8 15 8 15s8-9 8-15a8 8 0 0 0-8-8z" fill="none" stroke="#1b1d5a" stroke-width="1.8"/><circle cx="15" cy="11" r="3" fill="none" stroke="#1b1d5a" stroke-width="1.8"/></svg></div>
  <h3 class="card__title" style="top:42px">Local Love</h3>
  <p class="card__text" style="top:110px">We celebrate the heart of Michigan by partnering with local legends. Say hello to Pine Hollow Jerky and Lakeshore Crisp Chips—our hometown heroes. Their flavors dance on your taste buds, and we’re thrilled to bring them straight to your workplace.</p>
</article>

<article class="card" style="left:614px;top:1909px">
  <div class="card__icon"><svg width="30" height="30" viewBox="0 0 30 30"><circle cx="15" cy="12" r="8" fill="none" stroke="#1b1d5a" stroke-width="1.8"/><path d="M11 12l3 3 5-6" fill="none" stroke="#1b1d5a" stroke-width="1.8"/><path d="M10 19l-2 8 7-3 7 3-2-8" fill="none" stroke="#1b1d5a" stroke-width="1.8"/></svg></div>
  <h3 class="card__title" style="top:42px">Quality Meets Convenience</h3>
  <p class="card__text" style="top:110px">Imagine this: You’re mid-meeting, and your stomach growls. Fear not! SnackOrbit’s machines offer top-notch snacks and beverages. It’s like having a mini food festival at your fingertips.</p>
</article>

<article class="card" style="left:74px;top:2181px">
  <div class="card__icon"><svg width="30" height="30" viewBox="0 0 30 30"><circle cx="12" cy="10" r="5" fill="none" stroke="#1b1d5a" stroke-width="1.8"/><path d="M3 27c0-6 4-9 9-9s9 3 9 9" fill="none" stroke="#1b1d5a" stroke-width="1.8"/><rect x="19" y="6" width="9" height="7" rx="2" fill="none" stroke="#1b1d5a" stroke-width="1.6"/></svg></div>
  <h3 class="card__title" style="top:42px">Unleash Your Cravings</h3>
  <p class="card__text" style="top:108px">SnackOrbit isn’t bound by corporate ties. We’re the rebels of the vending world. Craving a bag of crispy, kettle-cooked chips? Done. Hankering for jerky that packs a punch? We’ve got you covered. Our machines are like treasure chests, waiting for you to unlock flavor magic.</p>
</article>

<article class="card" style="left:614px;top:2181px">
  <div class="card__icon"><svg width="30" height="30" viewBox="0 0 30 30"><rect x="5" y="4" width="16" height="21" rx="2" fill="none" stroke="#1b1d5a" stroke-width="1.8"/><circle cx="18" cy="18" r="5" fill="#fff" stroke="#1b1d5a" stroke-width="1.8"/><path d="M22 22l5 5" stroke="#1b1d5a" stroke-width="1.8"/></svg></div>
  <h3 class="card__title" style="top:34px">Pandemic-Proof<br>&amp; Recession-Ready</h3>
  <p class="card__text" style="top:117px">Life throws curveballs, but SnackOrbit stands strong. Our vending machines are the unsung heroes of resilience. Rain or shine, they’re there, serving up joy.</p>
</article>

<!-- cta band -->
<section class="band" style="top:2492px;height:364px">
  <div class="photo" style="inset:0;background:linear-gradient(90deg,#2a3358 0%,#3d4670 40%,#4a506e 60%,#2a3358 100%)" role="img" aria-label="Close-up of a stocked vending machine"></div>
  <div class="abs" style="inset:0;background:rgba(27,29,90,.45)"></div>
</section>
<h2 class="band__title display" style="top:2582px">Ready to Experience the SnackOrbit Difference?</h2>
<p class="band__text" style="top:2644px">Sign up now and let’s connect. Taste the future of snacking firsthand! Contact us today and explore how our vending magic can elevate your space.</p>
<a class="btn btn--orange" style="left:531px;top:2719px;width:138px;height:39px;font-size:20px">Sign Up</a>

<!-- contact -->
<svg class="abs" style="left:720px;top:2756px" width="480" height="505" viewBox="0 0 480 505" aria-hidden="true">
  <path d="M480 40 L480 505 L330 420 C280 440 230 450 200 445 C80 430 5 340 5 240 C5 110 110 5 250 5 C330 5 410 20 480 40 Z" fill="#2c5a2a"/>
</svg>
<div class="machine" style="left:831px;top:2792px;width:266px;height:446px" role="img" aria-label="Snack vending machine stocked with drinks and snacks"></div>

<h2 class="abs display contact__title">Contact Us</h2>
<div class="field" style="left:75px;top:2996px;width:254px">Full Name</div>
<div class="field" style="left:348px;top:2996px;width:252px">Email Address</div>
<div class="field" style="left:75px;top:3061px;width:254px">Phone No</div>
<div class="field" style="left:348px;top:3061px;width:252px">Subject</div>
<div class="field field--area" style="left:75px;top:3122px;width:525px">Message</div>
<a class="btn btn--green" style="left:75px;top:3247px;width:179px;height:46px">Submit</a>

<!-- questionnaire band -->
<section class="band" style="top:3361px;height:287px">
  <div class="photo" style="inset:0;background:linear-gradient(90deg,#1d3a1d 0%,#2e4f2a 35%,#3a5234 60%,#1c301e 100%)" role="img" aria-label="Person choosing a snack at a vending machine"></div>
  <div class="abs" style="inset:0;background:rgba(22,50,22,.4)"></div>
</section>
<h2 class="band__title display" style="top:3422px">Answer the Questionnaire for Those Interested<br>in Getting a Free Vending Machine</h2>
<a class="btn btn--orange" style="left:531px;top:3542px;width:138px;height:38px;font-size:20px">Contact Us</a>

<!-- footer -->
<footer>
  <div class="brand" style="left:76px;top:3722px;font-size:46px;color:var(--navy)"><span class="brand__dot" style="background:var(--green)"></span>SnackOrbit</div>
  <p class="abs" style="left:74px;width:234px;top:3803px;text-align:center;font-size:11.5px;line-height:24px">Copyright © 2024 SnackOrbit<br>All Right Reserved</p>

  <h4 class="foot-head" style="left:363px">Site Map</h4>
  <span class="foot-link" style="top:3744px">Home</span>
  <span class="foot-link" style="top:3779px">About SnackOrbit</span>
  <span class="foot-link" style="top:3814px">Why Choose SnackOrbit?</span>
  <span class="foot-link" style="top:3849px">Products &amp; Services</span>
  <span class="foot-link" style="top:3884px">Contact Us</span>

  <h4 class="foot-head" style="left:615px">Address</h4>
  <div class="foot-row" style="top:3741px"><svg width="14" height="14" viewBox="0 0 14 14"><path d="M7 1a4.5 4.5 0 0 0-4.5 4.5C2.5 9 7 13 7 13s4.5-4 4.5-7.5A4.5 4.5 0 0 0 7 1z" fill="#2c5a2a"/></svg><span>48 Birchwood Lane Suite 12,<br>Traverse Bay 49684, United States</span></div>
  <div class="foot-row" style="top:3800px"><svg width="14" height="14" viewBox="0 0 14 14"><path d="M3 1l3 3-1.5 2a8 8 0 0 0 3.5 3.5L10 8l3 3-2 2C6 13 1 8 1 3z" fill="#2c5a2a"/></svg><span>+1 555-010-2345</span></div>
  <div class="foot-row" style="top:3834px"><svg width="14" height="14" viewBox="0 0 14 14"><rect x="1" y="3" width="12" height="9" rx="1" fill="#2c5a2a"/><path d="M1.5 3.5L7 8l5.5-4.5" stroke="#fff" stroke-width="1.2" fill="none"/></svg><span>hello@snackorbit.example</span></div>

  <h4 class="foot-head" style="left:882px">Follow Us</h4>
  <div class="social" aria-label="Social media links"><span></span><span></span><span></span><span></span><span></span></div>
</footer>

</body>
</html>
```